Website for Excavator and Earthworks Company

We require a modern, sleek and practical website for our newly created earthworks/excavator business in Perth, Western Australia called Bluegum Ridge Earthworks.

The website should have a modern, cutting edge feel but only needs to be relatively simplistic in it's layout and eventual functionality.

Some pages it should have would be Home, About, Projects and Contact Us.

```html
<!DOCTYPE html>
<html lang="en">
<head>
<meta charset="utf-8">
<title>Bluegum Ridge Earthworks</title>
<link href="https://fonts.googleapis.com/css2?family=Unbounded:wght@600;800&family=Figtree:wght@400;500;600;700&display=swap" rel="stylesheet">
<style>
:root{
  --lime:#c6d82e;
  --lime-dark:#a9bb1c;
  --ink:#141414;
  --dark:#1f1f1f;
  --card-dark:#2d2d2b;
  --amber:#d8901b;
  --white:#ffffff;
  --muted:#5a5a5a;
  --line:#d6d6d6;
  --head:"Unbounded",sans-serif;
  --body:"Figtree",sans-serif;
}
*{margin:0;padding:0;box-sizing:border-box}
html,body{width:1200px;height:3950px;overflow:hidden;background:var(--white);font-family:var(--body);color:var(--ink)}
.page{position:relative;width:1200px;height:3950px}
.abs{position:absolute}
.brand{font-family:var(--body);font-weight:700;font-size:19px;letter-spacing:.5px;color:var(--ink);display:flex;align-items:center;gap:8px}
.brand .dot{width:14px;height:14px;background:var(--lime)}
/* header */
.header-brand{left:141px;top:44px;z-index:3}
.topbar{left:391px;top:0;width:809px;height:28px;background:var(--lime);clip-path:polygon(14px 0,100% 0,100% 100%,0 100%);display:flex;align-items:center;justify-content:flex-end;gap:30px;padding-right:141px;font-size:12.5px;z-index:3}
.topbar span{display:flex;align-items:center;gap:8px}
.nav{left:0;top:28px;width:1200px;height:61px;display:flex;align-items:center;justify-content:flex-end;padding-right:141px;gap:36px;font-size:13px;font-weight:500;z-index:2}
.nav .cta{background:var(--ink);color:var(--white);padding:10px 18px}
/* hero */
.hero-bg{left:0;top:89px;width:1200px;height:608px;background:linear-gradient(100deg,#2b2b29 0%,#4a4a44 40%,#7b7462 70%,#9a8a6a 100%);clip-path:polygon(0 0,100% 0,100% 558px,650px 578px,0 608px)}
.hero-stripe{left:650px;top:646px;width:550px;height:60px;background:var(--lime);clip-path:polygon(0 22px,100% 0,100% 12px,40px 60px)}
.hero-stripe2{left:650px;top:660px;width:100px;height:30px;background:#111;clip-path:polygon(0 12px,100% 4px,100% 14px,10px 30px)}
.hero-tag{left:141px;top:158px;background:rgba(255,255,255,.2);color:var(--white);font-size:12.5px;font-weight:600;padding:10px 18px}
.hero-title{left:141px;top:206px;font-family:var(--head);font-weight:800;font-size:40px;line-height:57px;color:var(--white)}
.hero-title em{font-style:normal;color:var(--lime)}
.hero-copy{left:141px;top:389px;border-left:2px solid var(--lime);padding-left:14px;width:440px;color:var(--white);font-size:16px;line-height:25px;font-weight:500}
.btn{display:inline-flex;align-items:center;gap:10px;font-size:14px;font-weight:600;padding:0 20px;height:46px}
.hero-btns{left:141px;top:504px;display:flex;gap:14px}
.btn-lime{background:var(--lime);color:var(--ink)}
.btn-white{background:var(--white);color:var(--ink)}
/* about */
.about-back{left:0;top:799px;width:402px;height:487px;background:linear-gradient(160deg,#3a3228,#1c1a17)}
.about-img{left:141px;top:842px;width:459px;height:400px;background:linear-gradient(180deg,#8fa9c6 0%,#d9b58a 55%,#6f4c2f 100%)}
.eyebrow{display:flex;align-items:center;gap:6px;color:var(--lime-dark);font-size:14px;font-weight:500}
.eyebrow:before{content:"";width:32px;height:1.5px;background:var(--lime)}
.eyebrow.both:after{content:"";width:32px;height:1.5px;background:var(--lime)}
.about-text{left:659px;top:838px;width:380px}
.about-text h2{font-family:var(--head);font-weight:800;font-size:30px;line-height:38px;margin:12px 0 14px}
.about-text h3{color:var(--lime-dark);font-size:15.5px;font-weight:600;margin-bottom:16px}
.about-text p{font-size:12.5px;line-height:23px}
.about-text .btn{margin-top:28px;height:38px;font-size:13px;font-weight:500;background:var(--lime)}
/* services */
.services-intro{left:0;top:1378px;width:413px;height:600px;background:linear-gradient(120deg,#3c3c38,#1a1a19)}
.services-intro .inner{position:absolute;left:99px;top:158px;width:250px;color:var(--white)}
.services-intro h2{font-family:var(--head);font-weight:800;font-size:32px;line-height:38px;margin:10px 0 22px}
.services-intro p{font-size:16px;line-height:28px}
.svc{width:262px;height:300px;padding:58px 34px 0 36px;color:var(--white)}
.svc.amber{background:var(--amber)}
.svc.dark{background:var(--card-dark)}
.svc .icon{width:54px;height:52px;border:3px solid var(--white);border-radius:6px;margin-bottom:26px}
.svc h4{font-family:var(--head);font-weight:600;font-size:17px;line-height:20px;margin-bottom:12px}
.svc p{font-size:12.5px;line-height:19px;opacity:.92}
/* projects */
.projects-head{left:0;top:2066px;width:1200px;text-align:center}
.projects-head .eyebrow{justify-content:center}
.projects-head h2{font-family:var(--head);font-weight:800;font-size:30px;margin-top:10px}
.proj{display:flex;flex-direction:column;justify-content:flex-end;padding:0 12px 16px 12px;color:var(--white)}
.proj h5{font-family:var(--head);font-weight:600;font-size:15px;margin-bottom:4px}
.proj p{font-size:12.5px;line-height:17px}
/* quote */
.quote-bg{left:0;top:2675px;width:1200px;height:662px;background:linear-gradient(180deg,#2b2a27,#1e1d1b 60%,#262521)}
.quote-head{left:0;top:2763px;width:1200px;text-align:center;color:var(--white)}
.quote-head .eyebrow{justify-content:center}
.quote-head h2{font-family:var(--head);font-weight:800;font-size:31px;margin:10px 0 12px}
.quote-head p{font-size:14.5px;line-height:22px}
.form{left:210px;top:2908px;width:492px;height:317px;background:var(--white)}
.field{position:absolute;font-size:12.5px;border-bottom:1px solid var(--line);height:34px}
.submit{position:absolute;left:328px;top:252px;width:164px;height:38px;background:var(--lime);font-weight:700;font-size:15px;display:flex;align-items:center;justify-content:center}
.contact-box{left:702px;top:2908px;width:288px;height:317px;background:var(--lime);padding:32px 0 0 46px}
.contact-box h4{font-family:var(--head);font-weight:800;font-size:16px;line-height:22px;margin-bottom:14px}
.ci{display:flex;gap:12px;align-items:flex-start;font-size:12.5px;line-height:18px;margin-bottom:14px}
.socials{display:flex;gap:10px;margin-top:16px}
.socials i{width:24px;height:24px;border:1.5px solid var(--ink);display:block}
/* newsletter */
.news{left:0;top:3426px;width:1200px;text-align:center}
.news h3{font-family:var(--head);font-weight:800;font-size:18.5px;color:#1b2a57;margin-bottom:18px}
.news p{font-size:14px;line-height:21px}
.news-input{left:357px;top:3524px;width:332px;height:38px;border:1px solid var(--line);font-size:12.5px;padding:11px 12px}
.news-btn{left:689px;top:3524px;width:154px;height:38px;background:var(--lime);font-family:var(--head);font-weight:800;font-size:14px;display:flex;align-items:center;justify-content:center}
/* footer */
.rule{left:141px;top:3612px;width:918px;height:1px;background:var(--line)}
.foot-brand{left:0;top:3690px;width:1190px;justify-content:center;font-size:22px}
.foot-img{left:856px;top:3628px;width:226px;height:160px;background:radial-gradient(ellipse at 55% 55%,#e08a2a 0%,#b86a22 35%,rgba(255,255,255,0) 70%)}
.foot-nav{left:0;top:3756px;width:1190px;display:flex;justify-content:center;gap:38px;font-size:13px;font-weight:500}
.foot-nav .on{color:var(--lime-dark)}
.foot-band{left:141px;top:3791px;width:918px;height:87px;background:var(--lime);display:flex;align-items:center;padding-left:176px;gap:60px}
.foot-band .ci{margin:0}
.copy{left:141px;top:3905px;font-size:12.5px}
.foot-social{left:925px;top:3896px;display:flex;gap:10px}
.foot-social i{width:24px;height:24px;border:1.5px solid var(--ink);display:block}
</style>
</head>
<body>
<div class="page">

  <!-- hero background -->
  <section class="abs hero-bg" role="img" aria-label="Orange excavator with auger attachment on dry Western Australian bushland"></section>
  <div class="abs hero-stripe"></div>
  <div class="abs hero-stripe2"></div>

  <!-- header -->
  <div class="abs brand header-brand"><span class="dot"></span>BLUEGUM RIDGE</div>
  <div class="abs topbar">
    <span><svg width="14" height="14" viewBox="0 0 24 24"><path d="M6 2l4 4-2 3c1 3 4 6 7 7l3-2 4 4-3 4C10 21 3 14 2 5z" fill="#141414"/></svg>Phone: (123) 456 7890 / (533) 456 1259</span>
    <span><svg width="15" height="12" viewBox="0 0 24 18"><rect x="1" y="1" width="22" height="16" fill="#141414"/><path d="M1 1l11 9 11-9" stroke="#c6d82e" stroke-width="2" fill="none"/></svg>Email Us On: info@bluegumridge-earthworks.example</span>
  </div>
  <nav class="abs nav">
    <span>HOME</span><span>ABOUT US</span><span>SERVICES</span><span>OUR PROJECT</span><span class="cta">CONTACT US →</span>
  </nav>

  <!-- hero content -->
  <div class="abs hero-tag">PERTH, WESTERN AUSTRALIA</div>
  <h1 class="abs hero-title">BLUEGUM RIDGE<br><em>EARTH MOVED</em><br>WITH <em>PRECISION</em></h1>
  <p class="abs hero-copy">Professional excavation, bulk earthworks, site preparation and land development services across Perth and Western Australia.</p>
  <div class="abs hero-btns"><span class="btn btn-lime">VIEW PROJECTS →</span><span class="btn btn-white">GET A QUOTE →</span></div>

  <!-- about -->
  <div class="abs about-back" role="img" aria-label="Dark close-up of excavator bucket in soil"></div>
  <div class="abs about-img" role="img" aria-label="Yellow excavator on a dirt mound at sunset"></div>
  <div class="abs about-text">
    <div class="eyebrow">ABOUT</div>
    <h2>BLUEGUM RIDGE EARTHWORKS</h2>
    <h3>Bluegum Ridge Earthworks: Building Perth's Future</h3>
    <p>Based in Perth, Western Australia, Bluegum Ridge Earthworks is a premier excavation and earthworks company specializing in residential, commercial, and industrial projects.</p>
    <p>With over 15 years of industry experience, our team combines cutting-edge equipment with skilled operators to deliver exceptional results on time and within budget.</p>
    <p>We pride ourselves on our commitment to safety, precision, and environmental responsibility in every project we undertake.</p>
    <span class="btn">CONTACT OUR TEAM</span>
  </div>

  <!-- services -->
  <div class="abs services-intro" role="img" aria-label="Excavator on a construction site under a cloudy sky">
    <div class="inner">
      <div class="eyebrow" style="color:var(--lime)">WHAT WE DO</div>
      <h2>OUR<br>SERVICES</h2>
      <p>Comprehensive earthmoving and excavation solutions for projects of all sizes across Perth and regional WA.</p>
    </div>
  </div>
  <div class="abs svc amber" style="left:413px;top:1378px"><div class="icon" role="img" aria-label="Excavator icon"></div><h4>Bulk<br>Earthworks</h4><p>Large-scale cut and fill operations, land levelling, and soil compaction for subdivisions and commercial developments.</p></div>
  <div class="abs svc dark" style="left:675px;top:1378px"><div class="icon" role="img" aria-label="Land clearing icon"></div><h4>Land<br>Clearing</h4><p>Vegetation removal, stump grinding, and site preparation for residential, agricultural and commercial properties.</p></div>
  <div class="abs svc dark" style="left:937px;top:1378px"><div class="icon" role="img" aria-label="Road icon"></div><h4>Road &amp; Driveway Construction</h4><p>Formation, grading and compaction for access roads, farm tracks, and residential driveways.</p></div>
  <div class="abs svc dark" style="left:413px;top:1678px"><div class="icon" role="img" aria-label="Dam icon"></div><h4>Dam<br>&amp; Drainage</h4><p>Dam construction, excavation, lining, and drainage solutions for flood mitigation and water management.</p></div>
  <div class="abs svc amber" style="left:675px;top:1678px"><div class="icon" role="img" aria-label="Site preparation icon"></div><h4>Site<br>Preparation</h4><p>Complete site preparation for residential and commercial construction, including slab foundations and pad preparation.</p></div>
  <div class="abs svc dark" style="left:937px;top:1678px"><div class="icon" role="img" aria-label="Material supply icon"></div><h4>Material<br>Supply &amp; Removal</h4><p>Supply of quality fill material, sand, gravel, and removal of excess spoil from your site.</p></div>

  <!-- projects -->
  <div class="abs projects-head"><div class="eyebrow both">CREATIONS</div><h2>OUR PROJECTS</h2></div>
  <div class="abs proj" style="left:141px;top:2172px;width:325px;height:157px;background:linear-gradient(180deg,#7a7a6e,#3c3a32)" role="img" aria-label="Excavator near a house in misty autumn forest"><h5>Lorem ipsum dolor sit amet,</h5><p>Duis autem vel eum iriure dolor in hendrerit in vulputate velit esse molestie consequat.</p></div>
  <div class="abs proj" style="left:141px;top:2340px;width:325px;height:240px;background:linear-gradient(180deg,#b9a88a,#4a3a28)" role="img" aria-label="Excavator at sunset on a dirt site"><h5>Lorem ipsum dolor sit amet,</h5><p>Duis autem vel eum iriure dolor in hendrerit in vulputate velit esse molestie consequat.</p></div>
  <div class="abs proj" style="left:477px;top:2172px;width:286px;height:228px;background:linear-gradient(180deg,#b08a5e,#5a3e24);padding-left:22px" role="img" aria-label="Aerial view of excavator digging in rocky soil"><h5>Lorem ipsum dolorsit</h5><p>Duis autem vel eum iriure dolor in hendrerit in vulputate velit esse mole.</p></div>
  <div class="abs proj" style="left:773px;top:2172px;width:286px;height:228px;background:linear-gradient(180deg,#5d6e3a,#3a3422);padding-left:18px" role="img" aria-label="Excavator clearing green vegetation"><h5>Lorem ipsum dolor amet</h5><p>Duis autem vel eum iriure dolor in hendrerit in vulputate velit esse mole.</p></div>
  <div class="abs proj" style="left:477px;top:2411px;width:582px;height:169px;background:linear-gradient(90deg,#6f7d52,#8a8a7a 50%,#4a4c45);padding-left:395px;justify-content:center" role="img" aria-label="Aerial view of road works beside houses"><h5>Lorem ipsum<br>dolor sit amet,</h5><p>Duis autem vel eum iriure dolor in hendrerit in vulputate velit esse molestie consequat.</p></div>

  <!-- quote -->
  <div class="abs quote-bg" role="img" aria-label="Dark construction site at dusk"></div>
  <div class="abs quote-head"><div class="eyebrow both" style="color:var(--lime)">QUICK INQUIRY</div><h2>REQUEST A QUOTE</h2><p>Ready to move earth? Contact our Perth team for a no-obligation<br>site assessment and quote.</p></div>
  <div class="abs form">
    <span class="field" style="left:26px;top:20px;width:205px">First name*</span>
    <span class="field" style="left:257px;top:20px;width:205px">Last name*</span>
    <span class="field" style="left:26px;top:76px;width:205px">Your phone*</span>
    <span class="field" style="left:257px;top:76px;width:205px">Your email*</span>
    <span class="field" style="left:26px;top:132px;width:436px;height:80px">Message</span>
    <span class="submit">SUBMIT NOW</span>
  </div>
  <div class="abs contact-box">
    <h4>CONTACT<br>INFORMATION</h4>
    <div class="ci"><svg width="22" height="26" viewBox="0 0 24 28"><path d="M12 1a9 9 0 0 0-9 9c0 7 9 16 9 16s9-9 9-16a9 9 0 0 0-9-9z" fill="#141414"/><circle cx="12" cy="10" r="3.5" fill="#c6d82e"/></svg><span>123, Building Name, Street<br>City, State XY 123456</span></div>
    <div class="ci"><svg width="22" height="22" viewBox="0 0 24 24"><path d="M6 2l4 4-2 3c1 3 4 6 7 7l3-2 4 4-3 4C10 21 3 14 2 5z" fill="none" stroke="#141414" stroke-width="2"/></svg><span>PHONE<br>(123) 456 7890</span></div>
    <div class="ci"><svg width="22" height="18" viewBox="0 0 24 18"><rect x="1" y="1" width="22" height="16" fill="#141414"/><path d="M1 1l11 9 11-9" stroke="#c6d82e" stroke-width="2" fill="none"/></svg><span>EMAIL<br>info@bluegumridge.example</span></div>
    <div class="socials" aria-label="Social links"><i></i><i></i><i></i><i></i></div>
  </div>

  <!-- newsletter -->
  <div class="abs news"><h3>SUBSCRIBE TO OUR NEWSLETTER</h3><p>Want to keep up to date with all our latest news and information?<br>Enter your email below to be added to our mailing list.</p></div>
  <div class="abs news-input">Enter your email address</div>
  <div class="abs news-btn">SUBSCRIBE</div>

  <!-- footer -->
  <div class="abs rule"></div>
  <div class="abs foot-img" role="img" aria-label="Orange excavator"></div>
  <div class="abs brand foot-brand"><span class="dot"></span>BLUEGUM RIDGE</div>
  <div class="abs foot-nav"><span class="on">HOME</span><span>ABOUT US</span><span>SERVICES</span><span>PROJECTS</span><span>CONTACT US</span></div>
  <div class="abs foot-band">
    <div class="ci"><svg width="22" height="26" viewBox="0 0 24 28"><path d="M12 1a9 9 0 0 0-9 9c0 7 9 16 9 16s9-9 9-16a9 9 0 0 0-9-9z" fill="#141414"/><circle cx="12" cy="10" r="3.5" fill="#c6d82e"/></svg><span>123, Building Name, Street<br>City, State XY 123456</span></div>
    <div class="ci"><svg width="22" height="22" viewBox="0 0 24 24"><path d="M6 2l4 4-2 3c1 3 4 6 7 7l3-2 4 4-3 4C10 21 3 14 2 5z" fill="none" stroke="#141414" stroke-width="2"/></svg><span>PHONE<br>(123) 456 7890</span></div>
    <div class="ci"><svg width="22" height="18" viewBox="0 0 24 18"><rect x="1" y="1" width="22" height="16" fill="#141414"/><path d="M1 1l11 9 11-9" stroke="#c6d82e" stroke-width="2" fill="none"/></svg><span>EMAIL<br>info@bluegumridge.example</span></div>
  </div>
  <div class="abs copy">© 2026 Bluegum Ridge Earthworks. All Rights Reserved.</div>
  <div class="abs foot-social" aria-label="Social links"><i></i><i></i><i></i><i></i></div>

</div>
</body>
</html>
```